Local Roofing/Construction company business needs new biz card design

We need a new business card design, current cards are from the start of this operation and generic at best. We are a local Construction Company (General Contractor) with a majority of our work originating from insurance claims-exterior finish work is the main focus (Roofs-Siding-Gutters etc). Heavily involved with homeowners and the low ball offers they receive from insurance company's after a insurable event takes place. I have attached some of our original logo file(s) below.

```html
<!DOCTYPE html>
<html lang="en">
<head>
<meta charset="utf-8">
<title>Stonefield Construction – Business Card</title>
<link href="https://fonts.googleapis.com/css2?family=Montserrat:wght@400;500;800&display=swap" rel="stylesheet">
<style>
  :root {
    --bg: #d8dbdb;
    --card: #f7f7f5;
    --green: #2a9a3c;
    --ink: #2b2b2b;
    --muted: #555;
  }
  * { margin: 0; padding: 0; box-sizing: border-box; }
  html, body { width: 1200px; height: 829px; overflow: hidden; }
  body {
    background: var(--bg);
    font-family: "Montserrat", sans-serif;
    color: var(--ink);
    position: relative;
  }
  .card {
    position: absolute;
    top: 266px;
    width: 520px;
    height: 297px;
    background: var(--card);
    box-shadow: 0 10px 24px rgba(0,0,0,.12);
  }
  .card--front { left: 60px; }
  .card--back { left: 620px; }

  /* front */
  .brand {
    position: absolute;
    left: 34px;
    top: 78px;
    width: 200px;
    display: flex;
    align-items: center;
    gap: 10px;
  }
  .brand__square { width: 22px; height: 22px; background: var(--green); flex: none; }
  .brand__name {
    color: var(--green);
    font-weight: 800;
    font-size: 17px;
    line-height: 1.15;
    text-transform: uppercase;
    letter-spacing: .5px;
  }
  .divider {
    position: absolute;
    left: 250px;
    top: 50px;
    width: 1px;
    height: 110px;
    background: var(--green);
  }
  .contact {
    position: absolute;
    left: 272px;
    top: 56px;
  }
  .contact__name {
    color: var(--green);
    font-weight: 800;
    font-size: 17px;
    letter-spacing: 1px;
    text-transform: uppercase;
  }
  .contact__title {
    font-size: 11px;
    color: var(--muted);
    margin-top: 2px;
    margin-bottom: 12px;
  }
  .contact__line {
    display: flex;
    align-items: center;
    gap: 7px;
    font-size: 11px;
    line-height: 20px;
  }
  .contact__line svg { width: 10px; height: 10px; fill: var(--green); flex: none; }
  .address {
    position: absolute;
    left: 34px;
    bottom: 34px;
    font-size: 11px;
    letter-spacing: .3px;
  }

  /* back */
  .brand.brand--large {
    left: 0;
    top: 0;
    width: 100%;
    height: 100%;
    flex-direction: column;
    align-items: center;
    justify-content: center;
    gap: 14px;
  }
  .brand--large .brand__square { width: 46px; height: 46px; }
  .brand--large .brand__name { font-size: 24px; text-align: center; }
</style>
</head>
<body>
  <section class="card card--front">
    <div class="brand">
      <span class="brand__square"></span>
      <span class="brand__name">Stonefield<br>Construction</span>
    </div>
    <div class="divider"></div>
    <div class="contact">
      <p class="contact__name">Marcus Hale</p>
      <p class="contact__title">Managing Director</p>
      <p class="contact__line">
        <svg viewBox="0 0 10 10"><path d="M2 0.5 L3.8 2.6 L2.8 3.8 Q4 6 6.2 7.2 L7.4 6.2 L9.5 8 L8.2 9.5 Q1 9 0.5 1.8 Z"/></svg>
        0491 570 112
      </p>
      <p class="contact__line">
        <svg viewBox="0 0 10 10"><path d="M0 2 H10 V8 H0 Z M0.8 2.6 L5 5.6 L9.2 2.6 Z" fill-rule="evenodd"/></svg>
        info@stonefieldbuild.com
      </p>
      <p class="contact__line">
        <svg viewBox="0 0 10 10"><circle cx="5" cy="5" r="4.6"/></svg>
        www.stonefieldbuild.com
      </p>
    </div>
    <p class="address">418 W Harbor Road Millbrook County 5120</p>
  </section>

  <section class="card card--back">
    <div class="brand brand--large">
      <span class="brand__square"></span>
      <span class="brand__name">Stonefield<br>Construction</span>
    </div>
  </section>
</body>
</html>
```